Retail Jewelry Business Card Design Project

We are in need of a new business card design for a retail jewelry store. This store is in the business of fine jewelry including but not specific to bridal jewelry, diamonds, designer jewelry and watches.

This store has been in business for 20 years but continues to strive for a modern professional appeal. The main colors use for this business are a royal blue, white and silver.

Target Market(s)

Target market is ages 18-50

Industry/Entity Type

Jewelry

Requirements
Must have
• Sales Person Name
Sales Person Email Address

Store Address
Store Phone
Website

Standard business card size. No odd shapes or sizes.
Nice to have
• Overall modern feel for card.

We have thought that a design with a nice feature of the logo on the back of the card would be nice but open to ideas.
Should not have
• No specific images of jewelry should be used.

```html
<!DOCTYPE html>
<html lang="en">
<head>
<meta charset="utf-8">
<title>Marlow Crane Fine Jewelry – Business Cards</title>
<link rel="stylesheet" href="https://fonts.googleapis.com/css2?family=Tinos:wght@400;700&family=Dancing+Script:wght@700&display=swap">
<style>
  :root {
    --royal-blue: #2e3192;
    --lavender: #7b78b8;
    --card-white: #ffffff;
    --backdrop: #e4e4ea;
    --silver-text: #4a4a4a;
    --serif: "Tinos", "Times New Roman", serif;
    --script: "Dancing Script", cursive;
  }
  * { margin: 0; padding: 0; box-sizing: border-box; }
  html, body { width: 1200px; height: 980px; overflow: hidden; }
  body { background: var(--backdrop); font-family: var(--serif); position: relative; }

  .card {
    position: absolute;
    width: 600px; height: 343px;
    background: var(--card-white);
    border-radius: 26px;
    overflow: hidden;
    box-shadow: 0 6px 18px rgba(0,0,0,0.12);
  }
  .card--back { left: 560px; top: 70px; }
  .card--front { left: 40px; top: 560px; }

  .brand { position: absolute; color: var(--royal-blue); font-weight: 700; text-align: center; line-height: 1; }
  .brand__name { display: block; font-size: 58px; letter-spacing: 1px; }
  .brand__tag { display: block; font-size: 25px; letter-spacing: 5px; margin-top: 10px; }

  .card--back .brand { left: 0; right: 0; top: 80px; }
  .website-line {
    position: absolute; left: 0; right: 0; top: 230px;
    text-align: center; font-size: 17px; letter-spacing: 5px; color: var(--silver-text);
  }

  .swoop { position: absolute; inset: 0; width: 100%; height: 100%; }
  .card--front .brand { left: 150px; right: 20px; top: 26px; }
  .card--front .brand__name { font-size: 50px; }
  .card--front .brand__tag { font-size: 22px; }

  .person-name {
    position: absolute; left: 40px; top: 106px;
    font-family: var(--script); font-size: 22px; line-height: 1.2; color: var(--royal-blue);
  }
  .contact {
    position: absolute; right: 34px; top: 234px;
    list-style: none; text-align: right; color: var(--card-white); font-size: 16px; line-height: 23px;
  }
  .contact li { display: flex; align-items: center; justify-content: flex-end; gap: 7px; }
  .contact svg { width: 13px; height: 13px; }
  .address {
    position: absolute; left: 40px; bottom: 16px;
    color: var(--card-white); font-size: 16px; line-height: 1.2;
  }
</style>
</head>
<body>
  <section class="card card--back" aria-label="Card back">
    <div class="brand">
      <span class="brand__name">Marlow Crane</span>
      <span class="brand__tag">FINE JEWELRY</span>
    </div>
    <p class="website-line">www.marlowcranejewelry.com</p>
  </section>

  <section class="card card--front" aria-label="Card front">
    <svg class="swoop" viewBox="0 0 600 343" preserveAspectRatio="none" aria-hidden="true">
      <path d="M0,105 C70,205 270,225 600,165 L600,343 L0,343 Z" fill="var(--lavender)"/>
      <path d="M0,122 C70,222 270,242 600,182 L600,343 L0,343 Z" fill="var(--card-white)"/>
      <path d="M0,132 C70,232 270,252 600,192 L600,343 L0,343 Z" fill="var(--royal-blue)"/>
    </svg>
    <div class="brand">
      <span class="brand__name">Marlow Crane</span>
      <span class="brand__tag">FINE JEWELRY</span>
    </div>
    <p class="person-name">Marlow Crane Ellison</p>
    <ul class="contact">
      <li>
        <svg viewBox="0 0 16 16" aria-hidden="true"><circle cx="8" cy="8" r="7.5" fill="#fff"/><path d="M5 4.5l2 2-1 1c.6 1.3 1.6 2.3 2.9 2.9l1-1 2 2-1.2 1.2C7.5 12.4 3.6 8.5 3.8 5.7z" fill="var(--royal-blue)"/></svg>
        555-014-2290
      </li>
      <li>
        <svg viewBox="0 0 16 16" aria-hidden="true"><circle cx="8" cy="8" r="7.5" fill="#fff"/><rect x="4" y="5" width="8" height="6" fill="none" stroke="var(--royal-blue)" stroke-width="1.2"/><path d="M4 5l4 3.5L12 5" fill="none" stroke="var(--royal-blue)" stroke-width="1.2"/></svg>
        marlow@marlowcranejewelry.com
      </li>
      <li>
        <svg viewBox="0 0 16 16" aria-hidden="true"><circle cx="8" cy="8" r="7" fill="none" stroke="#fff" stroke-width="1.3"/><ellipse cx="8" cy="8" rx="3" ry="7" fill="none" stroke="#fff" stroke-width="1"/><path d="M1 8h14" stroke="#fff" stroke-width="1"/></svg>
        www.marlowcranejewelry.com
      </li>
    </ul>
    <p class="address">2208 Bayview Avenue, Harbor City, FL 32499</p>
  </section>
</body>
</html>
```